A clean crisp business card for a Landscape Construction company. Designed to be easy to read contact/ info and also be appealing/interesting, unlike a traditional business card.

Industry/Entity Type

Landscape Construction

Contact Information for Business Card

Company name : Brambleford Landscape Construction, phone number: (877) 62Vista, website:Bramblefordyards.example, Email, sales@bramblefordyards.example

Requirements
Nice to have
• Luxurious finishes/ details…. Icons or emblems next to contact info
Should not have
• Clipart or general pictures

```html
<!DOCTYPE html>
<html lang="en">
<head>
<meta charset="utf-8">
<title>Brambleford Landscape Construction – Business Card</title>
<link rel="stylesheet" href="https://fonts.googleapis.com/css2?family=Cinzel:wght@600&family=Arimo:wght@400;700&display=swap">
<style>
  :root {
    --brand-blue: #1f6bb5;
    --deep-blue: #1a5ea3;
    --leaf-green: #8cc63f;
    --paper: #ffffff;
    --ink: #222222;
    --backdrop: #d3d3d3;
  }
  * { margin: 0; padding: 0; box-sizing: border-box; }
  html, body { width: 1200px; height: 788px; overflow: hidden; }
  body {
    background: var(--backdrop);
    position: relative;
    font-family: "Arimo", Arial, sans-serif;
  }
  .card {
    position: absolute;
    border-radius: 22px;
    overflow: hidden;
    box-shadow: 0 6px 18px rgba(0,0,0,0.18);
  }
  /* Front (portrait) */
  .card-front {
    left: 120px; top: 114px;
    width: 320px; height: 560px;
    background: var(--paper);
  }
  .front-swoosh { position: absolute; inset: 0; }
  .front-company {
    position: absolute;
    left: 0; right: 0; top: 268px;
    text-align: center;
    font-family: "Cinzel", Georgia, serif;
    font-weight: 600;
    color: var(--brand-blue);
    font-size: 17px;
    line-height: 1.35;
    letter-spacing: 0.04em;
  }
  .person {
    position: absolute;
    left: 0; right: 0; top: 352px;
    text-align: center;
  }
  .person-name {
    font-weight: 700;
    font-size: 24px;
    letter-spacing: 0.01em;
  }
  .person-name .first { color: var(--brand-blue); }
  .person-name .last { color: var(--leaf-green); }
  .person-role {
    font-size: 13px;
    color: var(--ink);
    margin-top: 2px;
  }
  .divider {
    position: absolute;
    left: 28px; right: 28px; top: 420px;
    display: flex; align-items: center; gap: 8px;
  }
  .divider .rule { flex: 1; height: 1px; background: var(--leaf-green); }
  .contact-icons { display: flex; gap: 4px; }
  .contact-icons svg { width: 16px; height: 16px; display: block; }
  .contact-list {
    position: absolute;
    left: 0; right: 0; top: 442px;
    list-style: none;
    text-align: center;
    font-size: 13px;
    line-height: 1.55;
    color: var(--ink);
  }
  /* Back (landscape) */
  .card-back {
    left: 520px; top: 244px;
    width: 560px; height: 320px;
    background: var(--brand-blue);
    display: flex; align-items: center; justify-content: center;
  }
  .back-company {
    font-family: "Cinzel", Georgia, serif;
    font-weight: 600;
    color: var(--paper);
    font-size: 34px;
    letter-spacing: 0.05em;
    text-align: center;
    line-height: 1.3;
  }
</style>
</head>
<body>
  <section class="card card-front" aria-label="Business card front">
    <svg class="front-swoosh" viewBox="0 0 320 560" aria-hidden="true">
      <path d="M130 0 C108 40 110 95 170 130 C240 170 300 200 320 265 L320 0 Z" fill="var(--brand-blue)"/>
      <path d="M124 0 C100 44 104 100 166 136 C236 176 294 206 320 270" fill="none" stroke="var(--leaf-green)" stroke-width="5"/>
      <path d="M116 12 C96 56 104 112 160 144 C226 182 284 214 316 280" fill="none" stroke="var(--deep-blue)" stroke-width="2"/>
    </svg>
    <div class="front-company">Brambleford<br>Landscape Construction</div>
    <div class="person">
      <div class="person-name"><span class="first">DANA</span> <span class="last">WHITLOW</span></div>
      <div class="person-role">Founder</div>
    </div>
    <div class="divider">
      <span class="rule"></span>
      <span class="contact-icons">
        <svg viewBox="0 0 16 16" aria-label="Phone"><rect width="16" height="16" rx="3" fill="var(--brand-blue)"/><path d="M5 4 L7 4 L7.5 6.5 L6.5 7.3 C7 8.5 7.8 9.3 9 9.8 L9.8 8.8 L12 9.3 L12 11.3 C8 11.5 4.6 8 5 4 Z" fill="#fff"/></svg>
        <svg viewBox="0 0 16 16" aria-label="Email"><rect width="16" height="16" rx="3" fill="var(--brand-blue)"/><rect x="3.5" y="5" width="9" height="6.5" fill="#fff"/><path d="M3.5 5 L8 8.6 L12.5 5" fill="none" stroke="var(--brand-blue)" stroke-width="1"/></svg>
        <svg viewBox="0 0 16 16" aria-label="Website"><rect width="16" height="16" rx="3" fill="var(--brand-blue)"/><circle cx="8" cy="8" r="4.3" fill="none" stroke="#fff" stroke-width="1.1"/><ellipse cx="8" cy="8" rx="1.8" ry="4.3" fill="none" stroke="#fff" stroke-width="0.9"/><line x1="3.7" y1="8" x2="12.3" y2="8" stroke="#fff" stroke-width="0.9"/></svg>
      </span>
      <span class="rule"></span>
    </div>
    <ul class="contact-list">
      <li>(877) 62Vista</li>
      <li>sales@bramblefordyards.example</li>
      <li>bramblefordyards.example</li>
    </ul>
  </section>

  <section class="card card-back" aria-label="Business card back">
    <div class="back-company">Brambleford<br>Landscape Construction</div>
  </section>
</body>
</html>
```